House flipping business web site needed

pinecrestholdingsgroup.example.
I am a residential developer in Northern NJ and I am looking for a fresh new updated website. I have an intro video about my company being made now. I don't update it very often but I want an easy format that I can add update photos to on projects I have worked on or homes I renovate for sale.

Target Market(s)

investors into my projects so a portfolio , people looking to sell their homes to me.

Industry/Entity Type

Real Estate Development

Number of Pages Required

4 page

Font styles to use
Serif

Colors
33b8a4
39a9d7
cadf82

Requirements
Must have
• space for an intro video about my company
• a portfolio with pictures and information about each project
• Markets we serve- Morris County, NJ
• My logo- already created
• SEO
• Yes I would like this to function over all platforms. Phone, computer, all platforms.
• history and background page
• I am looking for a completed page that I can upload to the site that hosts my website
Nice to have
• I want something creative, easy to navigate. modern.

```html
<!DOCTYPE html>
<html lang="en">
<head>
<meta charset="utf-8">
<title>Pinecrest Holdings Group</title>
<link rel="stylesheet" href="https://fonts.googleapis.com/css2?family=Bree+Serif&family=Roboto:wght@400;500;700&display=swap">
<style>
:root{
  --teal:#33b8a4;
  --blue:#39a9d7;
  --lime:#cadf82;
  --lime-dark:#b9d06a;
  --ink:#333333;
  --teal-ink:#1f8f80;
  --dark:#3a3a3a;
  --darker:#1e1e1e;
  --white:#ffffff;
  --serif:'Bree Serif', Georgia, serif;
  --sans:'Roboto', Arial, sans-serif;
}
*{margin:0;padding:0;box-sizing:border-box}
html,body{width:1200px;height:2647px;overflow:hidden}
body{position:relative;background:var(--white);font-family:var(--sans);color:var(--ink)}
.abs{position:absolute}

/* header */
.site-header{left:0;top:0;width:1200px;height:108px;background:var(--white);z-index:5}
.brand{left:130px;top:0;width:212px;height:172px;background:var(--white);z-index:6;display:flex;flex-direction:column;align-items:center;justify-content:center;box-shadow:0 2px 6px rgba(0,0,0,.15)}
.brand-name{font-family:var(--serif);color:var(--blue);font-size:26px;line-height:1.05;text-align:center}
.call{left:756px;top:18px;display:flex;align-items:center;gap:12px}
.call-icon{width:36px;height:36px;border-radius:50%;background:var(--teal);display:flex;align-items:center;justify-content:center}
.call-label{font-size:10px;font-weight:700;color:var(--ink)}
.call-number{font-size:18px;color:var(--teal)}
.search{left:945px;top:20px;width:122px;height:34px;border:1px solid #bbb;font-size:10px;color:#888;display:flex;align-items:center;padding-left:10px;gap:8px}
.nav{left:548px;top:66px;display:flex;gap:0;font-family:var(--serif);font-size:13px}
.nav a{color:var(--ink);text-decoration:none;padding:12px 23px;text-transform:uppercase}
.nav a.active{background:var(--lime)}

/* hero */
.hero{left:0;top:108px;width:1200px;height:520px;background:linear-gradient(180deg,#3d5a2c 0%,#6e7f5c 35%,#8a8676 50%,#4f7a2e 75%,#3f6a22 100%)}
.hero-title{left:0;top:405px;width:1200px;text-align:center;font-family:var(--serif);color:var(--white);font-size:32px;line-height:42px;text-shadow:0 2px 4px rgba(0,0,0,.5)}
.hero-arrow{top:333px;width:54px;height:54px;border-radius:50%;border:2px solid var(--white);background:rgba(0,0,0,.35);display:flex;align-items:center;justify-content:center}
.hero-dots{left:547px;top:523px;display:flex;gap:14px}
.hero-dots span{width:9px;height:9px;border-radius:50%;background:rgba(255,255,255,.6)}
.hero-dots span.on{background:var(--white)}

/* services */
.wave{left:0;width:1200px}
.services{left:0;top:620px;width:1200px;height:330px;background:var(--teal)}
.service{top:568px;width:320px;text-align:center}
.service-badge{width:132px;height:132px;border-radius:50%;background:var(--lime);border:6px solid var(--teal);margin:0 auto;display:flex;align-items:center;justify-content:center;box-shadow:0 0 0 4px rgba(255,255,255,.15)}
.service-title{margin-top:30px;font-family:var(--serif);font-size:19px;color:var(--lime)}
.service-text{margin:10px auto 0;width:270px;font-size:12.5px;line-height:19px;color:var(--white)}
.btn-outline{display:inline-block;margin-top:28px;padding:9px 14px;border:2px solid var(--lime);color:var(--lime);font-size:12px;font-family:var(--serif)}

/* welcome */
.welcome{left:0;top:950px;width:1200px;height:450px;background:var(--lime)}
.welcome-kicker{left:132px;top:998px;font-family:var(--serif);font-size:16px;color:var(--teal-ink)}
.welcome-title{left:132px;top:1018px;font-family:var(--serif);font-size:29px;letter-spacing:4px;color:var(--ink)}
.welcome-text{left:132px;top:1076px;width:334px;font-size:12.5px;line-height:19.5px;color:var(--ink);text-align:justify}
.btn-solid{left:132px;top:1280px;width:110px;height:40px;background:var(--teal);color:var(--white);font-size:12px;font-weight:700;display:flex;align-items:center;justify-content:center}
.video{left:507px;top:965px;width:560px;height:398px;background:linear-gradient(160deg,#7a8fa8 0%,#b08a5a 45%,#6a5c44 75%,#4d5d3c 100%)}
.video-play{left:237px;top:148px;width:104px;height:104px;border-radius:50%;border:6px solid rgba(255,255,255,.85);display:flex;align-items:center;justify-content:center}
.video-bar{left:0;bottom:0;width:560px;height:22px;background:#111;display:flex;align-items:center;padding:0 10px;gap:10px;color:var(--white);font-size:10px}
.video-track{flex:1;height:3px;background:#555;position:relative}
.video-track i{position:absolute;left:0;top:0;width:40%;height:3px;background:#ddd}

/* portfolio */
.portfolio{left:0;top:1385px;width:1200px;height:600px;background:linear-gradient(180deg,#3aa6d4,#2f92c2)}
.portfolio-title{left:128px;top:1450px;font-family:var(--serif);font-size:27px;letter-spacing:5px;color:var(--white)}
.pf-arrow{top:1447px;width:42px;height:42px;border-radius:50%;display:flex;align-items:center;justify-content:center}
.card{top:1512px;width:301px;height:390px;background:var(--white)}
.card-photo{width:301px;height:283px}
.card-text{padding:14px 24px;font-size:12px;line-height:18px;color:var(--ink)}

/* markets */
.markets-title{left:128px;top:2016px;font-family:var(--serif);font-size:27px;color:var(--blue)}
.markets-text{left:130px;top:2066px;width:560px;font-size:12.5px;line-height:20px}
.contact{left:128px;top:2145px;display:flex;align-items:center}
.contact-icon{width:54px;height:54px;border-radius:50%;background:var(--lime);display:flex;align-items:center;justify-content:center}
.contact-rule{width:1px;height:70px;background:#ccc;margin:0 24px}
.contact-name{font-size:13.5px}
.contact-phone{margin-top:10px;font-size:18px;font-weight:500;color:var(--blue)}
.market-map{left:762px;top:2003px;width:300px;height:262px;background:var(--lime);border-radius:40% 30% 45% 35%}

/* footer */
.footer{left:0;top:2320px;width:1200px;height:280px;background:var(--dark)}
.footer-brand{left:128px;top:2355px;width:250px;height:190px;display:flex;align-items:center;justify-content:center;gap:10px}
.footer-brand .dot{width:16px;height:16px;border-radius:50%;background:var(--blue)}
.footer-brand span{font-family:var(--serif);color:var(--blue);font-size:24px;line-height:1.1;text-align:center}
.footer-rule{top:2345px;width:1px;height:210px;background:#555}
.footer-menu{left:460px;top:2370px;width:200px;text-align:center;color:var(--white)}
.footer-menu h4{font-size:12.5px;font-weight:700;margin-bottom:20px}
.footer-menu li{list-style:none;font-size:11px;line-height:24px}
.newsletter{left:742px;top:2370px;width:326px;color:var(--white)}
.newsletter h4{text-align:center;font-size:12.5px;font-weight:700}
.email{margin-top:32px;height:48px;background:#5c5c5c;display:flex;align-items:center;padding-left:18px;gap:14px;font-size:11px;color:#ddd}
.signup{margin-top:12px;height:48px;background:var(--teal);display:flex;align-items:center;justify-content:center;font-family:var(--serif);font-size:21px}
.bottom-bar{left:0;top:2600px;width:1200px;height:47px;background:var(--darker);color:var(--white);font-size:10px}
.follow{left:130px;top:17px;display:flex;align-items:center;gap:8px}
.follow i{width:17px;height:17px;border-radius:50%;display:inline-block}
.copyright{left:872px;top:18px;font-weight:700}
</style>
</head>
<body>

<header class="abs site-header">
  <div class="abs call">
    <div class="call-icon"><svg width="16" height="16" viewBox="0 0 24 24"><path fill="#fff" d="M6.6 10.8a15.1 15.1 0 0 0 6.6 6.6l2.2-2.2c.3-.3.7-.4 1-.2 1.1.4 2.3.6 3.6.6.6 0 1 .4 1 1V20c0 .6-.4 1-1 1A17 17 0 0 1 3 4c0-.6.4-1 1-1h3.5c.6 0 1 .4 1 1 0 1.3.2 2.5.6 3.6.1.3 0 .7-.2 1z"/></svg></div>
    <div><div class="call-label">CALL US</div><div class="call-number">(888) 555-0199</div></div>
  </div>
  <div class="abs search"><svg width="10" height="10" viewBox="0 0 24 24"><circle cx="10" cy="10" r="7" stroke="#666" stroke-width="3" fill="none"/><path d="M15 15l7 7" stroke="#666" stroke-width="3"/></svg>SEARCH</div>
  <nav class="abs nav">
    <a class="active">Home</a><a>About Us</a><a>Services</a><a>Portfolio</a><a>Contact Us</a>
  </nav>
</header>
<div class="abs brand"><div class="brand-name">PINECREST<br>HOLDINGS GROUP</div></div>

<section class="abs hero" role="img" aria-label="Photo of a weathered single-storey house in an overgrown wooded yard"></section>
<h1 class="abs hero-title">WE WILL HELP YOU GET OUT OF<br>YOUR UNWANTED HOME</h1>
<div class="abs hero-arrow" style="left:82px"><svg width="16" height="16" viewBox="0 0 24 24"><path d="M15 4l-8 8 8 8" stroke="#fff" stroke-width="3" fill="none"/></svg></div>
<div class="abs hero-arrow" style="left:1066px"><svg width="16" height="16" viewBox="0 0 24 24"><path d="M9 4l8 8-8 8" stroke="#fff" stroke-width="3" fill="none"/></svg></div>
<div class="abs hero-dots"><span></span><span class="on"></span><span></span><span></span><span></span></div>

<section class="abs services"></section>
<svg class="abs wave" style="top:560px" width="1200" height="70" viewBox="0 0 1200 70"><path d="M0 70V40C150 5 300 5 450 30S750 70 900 35 1100 0 1200 20V70Z" fill="#33b8a4"/></svg>

<div class="abs service" style="left:103px">
  <div class="service-badge"><svg width="62" height="56" viewBox="0 0 62 56"><rect x="4" y="4" width="54" height="36" rx="4" fill="none" stroke="#fff" stroke-width="3"/><path d="M18 40l-6 12 16-12" fill="none" stroke="#fff" stroke-width="3"/><path d="M16 16h30M16 24h30M16 32h20" stroke="#fff" stroke-width="3"/></svg></div>
  <div class="service-title">HOW WE CAN HELP</div>
  <p class="service-text">Do you need to sell your home fast to avoid foreclosure, have estate home you do not want to fix to put on the market...</p>
  <span class="btn-outline">READ MORE</span>
</div>
<div class="abs service" style="left:440px">
  <div class="service-badge"><svg width="64" height="64" viewBox="0 0 64 64"><circle cx="32" cy="32" r="27" fill="none" stroke="#fff" stroke-width="3"/><text x="32" y="44" text-anchor="middle" font-family="Roboto,Arial,sans-serif" font-size="34" font-weight="700" fill="#fff">$</text></svg></div>
  <div class="service-title">FINANCING</div>
  <p class="service-text">We can close quickly and we buy with Cash We bring excellence to the home buying and renovation business.</p>
  <span class="btn-outline">READ MORE</span>
</div>
<div class="abs service" style="left:775px">
  <div class="service-badge"><svg width="62" height="60" viewBox="0 0 62 60"><path d="M6 30L31 6l25 24" fill="none" stroke="#fff" stroke-width="3"/><path d="M12 26v30h38V26" fill="none" stroke="#fff" stroke-width="3"/><rect x="25" y="36" width="12" height="20" fill="none" stroke="#fff" stroke-width="3"/></svg></div>
  <div class="service-title">WHAT WE DO</div>
  <p class="service-text">We are a team of experienced home buyers and renovators in the Morris County, NJ area. Our specialty is purchasing distressed...</p>
  <span class="btn-outline">READ MORE</span>
</div>

<section class="abs welcome"></section>
<svg class="abs wave" style="top:880px" width="1200" height="80" viewBox="0 0 1200 80"><path d="M0 80V20C200 70 400 70 600 40S950 0 1200 45V80Z" fill="#cadf82"/></svg>
<div class="abs welcome-kicker">WELCOME TO</div>
<h2 class="abs welcome-title">PINECREST</h2>
<p class="abs welcome-text">We are a team of experienced home buyers and renovators in the Morris County, NJ area. Our specialty is purchasing distressed homes and property. We then collaborate with the best talents in Northern New Jersey to renovate those properties and transform them into the best house in the neighborhood. As a result we create equity, a return on investment and most importantly we give home buyers a worry free property that provides a better way of life and hope for their future.</p>
<div class="abs btn-solid">READ MORE</div>
<div class="abs video" role="img" aria-label="Intro video still of a timber-framed house under construction among trees">
  <div class="abs video-play"><svg width="40" height="46" viewBox="0 0 40 46"><path d="M4 2l34 21L4 44Z" fill="#fff"/></svg></div>
  <div class="abs video-bar"><svg width="9" height="10" viewBox="0 0 9 10"><path d="M0 0l9 5-9 5Z" fill="#fff"/></svg><div class="video-track"><i></i></div><span>1:30 - 4:23</span></div>
</div>

<section class="abs portfolio" role="img" aria-label="Faint background photo of a renovated house"></section>
<svg class="abs wave" style="top:1355px" width="1200" height="60" viewBox="0 0 1200 60"><path d="M0 60V30C200 0 400 0 600 25S1000 55 1200 15V60Z" fill="#39a9d7"/></svg>
<h2 class="abs portfolio-title">PORTFOLIO</h2>
<div class="abs pf-arrow" style="left:962px;background:#fff"><svg width="14" height="14" viewBox="0 0 24 24"><path d="M15 4l-8 8 8 8" stroke="#333" stroke-width="3" fill="none"/></svg></div>
<div class="abs pf-arrow" style="left:1015px;background:var(--lime)"><svg width="14" height="14" viewBox="0 0 24 24"><path d="M9 4l8 8-8 8" stroke="#fff" stroke-width="3" fill="none"/></svg></div>

<article class="abs card" style="left:132px">
  <div class="card-photo" role="img" aria-label="Photo of a renovated two-storey house with stone wall and lawn" style="background:linear-gradient(180deg,#dfe6ee,#b9ae92 55%,#4f7a30)"></div>
  <p class="card-text">Many upgrades to this home, Added a new full bath, family room, office, kitchenette and kids play room in walk out basement with 2 triple french doors.</p>
</article>
<article class="abs card" style="left:448px">
  <div class="card-photo" role="img" aria-label="Photo of a new kitchen with wooden cabinets and island" style="background:linear-gradient(180deg,#c89a5e,#9a5426 55%,#6e2c12)"></div>
  <p class="card-text">House was torn down. Using portions of the foundation and an existing fireplace and chimney from the original home, a new house was constructed.</p>
</article>
<article class="abs card" style="left:765px">
  <div class="card-photo" role="img" aria-label="Photo of a remodelled colonial house with front garden" style="background:linear-gradient(180deg,#e9eef2,#bfc2b6 55%,#5c7a3a)"></div>
  <p class="card-text">A complete remodel and add on to this 2 bed-room house.</p>
</article>

<svg class="abs wave" style="top:1935px" width="1200" height="60" viewBox="0 0 1200 60"><path d="M0 0V40C200 60 400 55 600 30S1000 0 1200 35V0Z" fill="#2f92c2"/></svg>

<h2 class="abs markets-title">MARKETS WE SERVE</h2>
<p class="abs markets-text">Lorem Ipsum is simply dummy text of the printing and typesetting industry. Lorem Ipsum has been the industry's standard dummy</p>
<div class="abs contact">
  <div class="contact-icon"><svg width="18" height="18" viewBox="0 0 24 24"><path fill="#333" d="M6.6 10.8a15.1 15.1 0 0 0 6.6 6.6l2.2-2.2c.3-.3.7-.4 1-.2 1.1.4 2.3.6 3.6.6.6 0 1 .4 1 1V20c0 .6-.4 1-1 1A17 17 0 0 1 3 4c0-.6.4-1 1-1h3.5c.6 0 1 .4 1 1 0 1.3.2 2.5.6 3.6.1.3 0 .7-.2 1z"/></svg></div>
  <div class="contact-rule"></div>
  <div><div class="contact-name">Pinecrest Holdings Group &nbsp;|&nbsp; Morris County, NJ</div><div class="contact-phone">973-555-0142</div></div>
</div>
<div class="abs market-map" role="img" aria-label="Map of Morris County, New Jersey"></div>

<footer class="abs footer"></footer>
<svg class="abs wave" style="top:2280px" width="1200" height="60" viewBox="0 0 1200 60"><path d="M0 60V10C200 50 400 55 600 30S1000 0 1200 25V60Z" fill="#3a3a3a"/></svg>
<div class="abs footer-brand"><i class="dot"></i><span>PINECREST<br>HOLDINGS GROUP</span></div>
<div class="abs footer-rule" style="left:460px"></div>
<div class="abs footer-rule" style="left:685px"></div>
<div class="abs footer-menu">
  <h4>MENU</h4>
  <ul><li>Home</li><li>About Us</li><li>Services</li><li>Portfolio</li><li>Contact Us</li></ul>
</div>
<div class="abs newsletter">
  <h4>NEWSLETTER SIGNUP!</h4>
  <div class="email"><svg width="12" height="10" viewBox="0 0 12 10"><rect x=".5" y=".5" width="11" height="9" fill="none" stroke="#ddd"/><path d="M.5.5L6 5l5.5-4.5" fill="none" stroke="#ddd"/></svg>E-mail id</div>
  <div class="signup">SIGNUP!</div>
</div>
<div class="abs bottom-bar">
  <div class="abs follow">FOLLOW : <i style="background:#3b5998"></i><i style="background:#1da1f2"></i><i style="background:#dd4b39"></i><i style="background:#0077b5"></i></div>
  <div class="abs copyright">Copyrights @ 2016 All Rights Reserved</div>
</div>

</body>
</html>
```